sydney wedding photography business needs a business card design

we need a business card design for a sydney based wedding photography and videography business. our business name is :golden hour studio and film. our target clients are 24-35 yrs female. our style is candid, organic, natural, dynamic. we are a team of young photographers and videographers, and help brides to create memories that they will cherish for the rest of their lives. the logo will be provided. we want an elegant design that reflects our style, and also want to give a great impression to our clients that we are one of the best studios in sydney and our brand means quality and premium service.

Target Market(s)

bride to be, 24-35 years old, living in sydney and surrunding areas

Industry/Entity Type

Wedding Photography

Contact Information for Business Card

address: 57 tarrant street, glenmore nsw 2047
mobile: 0431872259
phone: (02) 9163 2408
info@tidewillowstudio.net.au
www.tidewillowstudio.net.au
facebook:tidewillowweddings
instagram:tidewillowweddings

Font styles to use
Serif
Sans Serif

Requirements
Nice to have
• maybe add my slogan"memories beyond eternity" if the layout looks good
Should not have
• no black color, not good idea for wedding biz card

```html
<!DOCTYPE html>
<html lang="en">
<head>
<meta charset="utf-8">
<title>Golden Hour Studio and Film — Business Card</title>
<link rel="stylesheet" href="https://fonts.googleapis.com/css2?family=Source+Sans+3:wght@400;600&display=swap">
<style>
  :root {
    --backdrop: #181818;
    --card-white: #ffffff;
    --card-amber: #966400;
    --gold: #e0a30b;
    --gold-deep: #c08a06;
    --gold-bright: #e9b514;
    --ink: #3a3a3a;
    --watermark-light: #ececec;
    --watermark-amber: #a06d05;
    --shadow: rgba(0, 0, 0, 0.55);
  }
  * { margin: 0; padding: 0; box-sizing: border-box; }
  html, body {
    width: 1200px;
    height: 900px;
    overflow: hidden;
    background: var(--backdrop);
    font-family: "Source Sans 3", "Myriad Pro", Arial, sans-serif;
  }
  .stage { position: relative; width: 1200px; height: 900px; }

  .card {
    position: absolute;
    top: 306px;
    width: 439px;
    height: 271px;
    border-radius: 10px;
    box-shadow: 2px 3px 4px var(--shadow);
    overflow: hidden;
  }
  .card--front { left: 139px; background: var(--card-white); }
  .card--back  { left: 608px; background: var(--card-amber); }

  .watermark {
    position: absolute;
    border-radius: 50%;
  }
  .card--front .watermark {
    left: 262px;
    top: 52px;
    width: 220px;
    height: 220px;
    background: var(--watermark-light);
  }
  .card--back .watermark {
    left: -20px;
    top: 46px;
    width: 200px;
    height: 200px;
    background: var(--watermark-amber);
  }

  .brand-mark {
    position: absolute;
    left: 30px;
    top: 82px;
    width: 150px;
    text-align: center;
    color: var(--gold-deep);
    font-weight: 600;
    font-size: 19px;
    line-height: 1.2;
  }
  .brand-mark__dot {
    display: block;
    width: 12px;
    height: 12px;
    margin: 0 auto 10px;
    border-radius: 50%;
    background: var(--gold-deep);
  }

  .divider {
    position: absolute;
    left: 196px;
    top: 66px;
    width: 1px;
    height: 140px;
    background: linear-gradient(to bottom, rgba(224,163,11,0), var(--gold) 40%, rgba(224,163,11,0));
  }

  .details {
    position: absolute;
    left: 228px;
    top: 50px;
    color: var(--ink);
    font-size: 12.5px;
    line-height: 15px;
  }
  .details__name { color: var(--gold); font-weight: 600; font-size: 15px; line-height: 18px; }
  .details__role { margin-bottom: 11px; }
  .details__address { margin-bottom: 11px; }
  .contact-line { display: flex; align-items: center; gap: 7px; }
  .contact-line svg { width: 9px; height: 9px; flex: none; }

  .back-name {
    position: absolute;
    left: 0;
    right: 0;
    top: 106px;
    text-align: center;
    color: var(--gold-bright);
    font-weight: 600;
    font-size: 30px;
    line-height: 1.1;
  }
</style>
</head>
<body>
<main class="stage">
  <section class="card card--front">
    <span class="watermark" aria-hidden="true"></span>
    <div class="brand-mark">
      <span class="brand-mark__dot"></span>
      Golden Hour<br>Studio and Film
    </div>
    <div class="divider"></div>
    <div class="details">
      <p class="details__name">Amelia Hart</p>
      <p class="details__role">Managing Director</p>
      <p class="details__address">57 Tarrant Street<br>Glenmore NSW 2047</p>
      <p class="contact-line">
        <svg viewBox="0 0 10 10" aria-hidden="true"><path fill="#e0a30b" d="M2 .5l1.6 2-1 1.1a6 6 0 0 0 3.8 3.8l1.1-1 2 1.6-1 1.5C4.6 9.5.5 5.4.5 1.5z"/></svg>
        (02) 9163 2408
      </p>
      <p class="contact-line">
        <svg viewBox="0 0 10 10" aria-hidden="true"><rect x="2.2" y="0.5" width="5.6" height="9" rx="1" fill="#e0a30b"/><rect x="3.2" y="1.6" width="3.6" height="5.6" fill="#fff"/></svg>
        0431 872 259
      </p>
      <p class="contact-line">
        <svg viewBox="0 0 10 10" aria-hidden="true"><rect x="0.5" y="2" width="9" height="6.5" fill="#e0a30b"/><path d="M0.8 2.4L5 5.6l4.2-3.2" fill="none" stroke="#fff" stroke-width="0.9"/></svg>
        info@tidewillowstudio.net.au
      </p>
      <p class="contact-line">
        <svg viewBox="0 0 10 10" aria-hidden="true"><circle cx="5" cy="5" r="4.5" fill="#e0a30b"/><path d="M0.8 5h8.4M5 .6c-2.2 2.4-2.2 6.4 0 8.8M5 .6c2.2 2.4 2.2 6.4 0 8.8" fill="none" stroke="#fff" stroke-width="0.7"/></svg>
        www.tidewillowstudio.net.au
      </p>
      <p class="contact-line">
        <svg viewBox="0 0 10 10" aria-hidden="true"><circle cx="5" cy="5" r="4.5" fill="#e0a30b"/></svg>
        tidewillowweddings
      </p>
    </div>
  </section>

  <section class="card card--back">
    <span class="watermark" aria-hidden="true"></span>
    <p class="back-name">Golden Hour Studio and Film</p>
  </section>
</main>
</body>
</html>
```